Stylish Business Cards Wanted

- DOUBLE SIDED Design Required -

High end, edgy cards for a corporate and personal stylist. Must include logo,
Name: Belinda Harwick
Title: Director and Stylist
telephone : +61 8 7142 5809
email: belinda@theloombriefing.example
website: theloombriefing.example
Tag: Corporate Workwear & Uniform Specialist | Personal Stylist
Would like nice icons for telephone, email, website

Target Market(s)

Businesses wanting stylish uniforms, people wanting stylish wardrobes

Industry/Entity Type

Corporate Workwear Stylist

Contact Information for Business Card

I would like black, white and gold foiling incorporated in the design - possibly a touch of the other colours on my branding guide attached Name: Belinda Harwick Title: Director and Stylist telephone : +61 8 7142 5809 email: belinda@theloombriefing.example website: theloombriefing.example Tag: Corporate Workwear & Uniform Specialist | Personal Stylist Would like nice icons for telephone, email, website

Font styles to use
Other font styles liked:
• Raleway

Colors

Designer to choose colors to be used in the design.

Requirements
Must have
• Gold foil accents

```html
<!DOCTYPE html>
<html lang="en">
<head>
<meta charset="utf-8">
<title>The Loom Briefing – Business Cards</title>
<link rel="stylesheet" href="https://fonts.googleapis.com/css2?family=Raleway:wght@400;500;600;700&display=swap">
<style>
  :root {
    --ink: #231f20;
    --paper: #ffffff;
    --gold: #e2b84a;
    --gold-deep: #c99a2e;
    --stage: #3a3a3a;
    --divider: #e4e4e4;
  }
  * { box-sizing: border-box; margin: 0; padding: 0; }
  html, body { width: 1200px; height: 1015px; overflow: hidden; }
  body {
    background: var(--stage);
    font-family: "Raleway", Arial, sans-serif;
    position: relative;
  }
  .card {
    position: absolute;
    left: 240px;
    width: 720px;
    height: 411px;
    overflow: hidden;
    box-shadow: 0 10px 30px rgba(0,0,0,.45);
  }
  /* Back of card */
  .card--back {
    top: 60px;
    background: var(--ink);
    display: flex;
    align-items: center;
    justify-content: center;
  }
  .brand {
    display: flex;
    align-items: center;
    gap: 16px;
    font-weight: 600;
    letter-spacing: .02em;
  }
  .brand__dot {
    width: 18px; height: 18px; border-radius: 50%;
  }
  .card--back .brand { color: var(--gold); font-size: 46px; }
  .card--back .brand__dot { background: var(--gold); width: 22px; height: 22px; }

  /* Front of card */
  .card--front {
    top: 520px;
    background: var(--paper);
  }
  .front__logo {
    position: absolute;
    left: 0; top: 0;
    width: 330px; height: 330px;
    display: flex; align-items: center; justify-content: center;
  }
  .card--front .brand { color: var(--ink); font-size: 27px; gap: 10px; }
  .card--front .brand__dot { background: var(--gold); width: 12px; height: 12px; }
  .front__divider {
    position: absolute;
    left: 330px; top: 40px;
    width: 1px; height: 230px;
    background: var(--divider);
  }
  .contact {
    position: absolute;
    left: 370px; top: 70px;
    color: var(--ink);
  }
  .contact__name {
    color: var(--gold);
    font-size: 27px;
    font-weight: 600;
    text-transform: uppercase;
    letter-spacing: .01em;
  }
  .contact__title {
    font-size: 19px;
    font-weight: 500;
    margin-top: 2px;
  }
  .contact__list {
    list-style: none;
    margin-top: 26px;
    font-size: 17px;
    font-weight: 500;
    line-height: 26px;
  }
  .contact__list li { display: flex; align-items: center; gap: 10px; }
  .contact__list svg { width: 16px; height: 16px; flex: none; }
  .tagline {
    position: absolute;
    left: 0; bottom: 0;
    width: 100%; height: 81px;
    background: var(--ink);
    border-top: 4px solid var(--gold);
    color: var(--paper);
    font-size: 19px;
    font-weight: 500;
    display: flex; align-items: center; justify-content: center;
    gap: 16px;
  }
  .tagline__sep {
    width: 7px; height: 7px; border-radius: 50%; background: var(--gold);
  }
</style>
</head>
<body>

<section class="card card--back" aria-label="Card back">
  <div class="brand">
    <span class="brand__dot"></span>
    <span class="brand__name">The Loom Briefing</span>
  </div>
</section>

<section class="card card--front" aria-label="Card front">
  <div class="front__logo">
    <div class="brand">
      <span class="brand__dot"></span>
      <span class="brand__name">The Loom Briefing</span>
    </div>
  </div>
  <div class="front__divider"></div>

  <div class="contact">
    <h1 class="contact__name">Belinda Harwick</h1>
    <p class="contact__title">Director and Stylist</p>
    <ul class="contact__list">
      <li>
        <svg viewBox="0 0 16 16" aria-hidden="true"><path fill="var(--gold)" d="M3.6 1.5l2.2 2.6-1.3 1.6c.8 1.9 2.2 3.3 4.1 4.1l1.6-1.3 2.6 2.2-1.2 2.3C6.7 13.2 2.8 9.3 2 4.6z"/></svg>
        <span>+61 8 7142 5809</span>
      </li>
      <li>
        <svg viewBox="0 0 16 16" aria-hidden="true"><rect x="1" y="3" width="14" height="10" fill="var(--gold)"/><path d="M1.5 3.5L8 9l6.5-5.5" fill="none" stroke="#fff" stroke-width="1.2"/></svg>
        <span>belinda@theloombriefing.example</span>
      </li>
      <li>
        <svg viewBox="0 0 16 16" aria-hidden="true"><g fill="none" stroke="var(--gold)" stroke-width="1.3"><circle cx="8" cy="8" r="6.5"/><ellipse cx="8" cy="8" rx="2.8" ry="6.5"/><path d="M1.5 8h13M2.5 4.8h11M2.5 11.2h11"/></g></svg>
        <span>theloombriefing.example</span>
      </li>
    </ul>
  </div>

  <div class="tagline">
    <span>Corporate Workwear &amp; Uniform Specialist</span>
    <span class="tagline__sep"></span>
    <span>Personal Stylist</span>
  </div>
</section>

</body>
</html>
```